I need a book cover (front and back) for a book I wrote called "7 Laws of Polish: A Closet Map for Triumph".

The short version of the book can be found online here: https://filebin.example.net/file/d/7KqPzR2mXwT9bLcN4vHs8YdJ3fGeA0uWi/view

I'm working on expanding this into a real book (100+ pages, with images), and putting it on Pellora.

I'm the author, Joel Mackworth. I was named "Sharpest Gent of the Nation" by Dapperly Journal, and I would like to add that to the cover for credibility.

My website "About Page" has more info about me and my business Threadwell House: https://threadwellhouse.example/pages/about-us

I also attached the first version of the cover I made using Canva.

I have LOTS of images, if you need some (mannequins, models, garments, etc). See our website's blog for more ideas of the images we have: https://threadwellhouse.example/blogs/news

```html
<!DOCTYPE html>
<html lang="en">
<head>
<meta charset="utf-8">
<title>7 Laws of Polish — Book Cover Wrap</title>
<link href="https://fonts.googleapis.com/css2?family=Playfair+Display:wght@400;500&family=Questrial&family=Montserrat:wght@500;600&display=swap" rel="stylesheet">
<style>
  :root{
    --backdrop:#4a4a4a;
    --cover-top:#7a6f67;
    --cover-bottom:#8b8079;
    --gold:#c4a678;
    --ivory:#ece6dc;
    --rule:#d9d1c4;
    --photo-deep:#5a3a2c;
    --photo-mid:#7b5a48;
    --portrait:#3e4650;
    --code-box:#ffffff;
  }
  *{margin:0;padding:0;box-sizing:border-box}
  html,body{width:1200px;height:740px;overflow:hidden;background:var(--backdrop)}
  .wrap{position:absolute;left:103px;top:30px;width:994px;height:680px;display:flex}
  .panel{position:relative;height:680px;background:linear-gradient(180deg,var(--cover-top),var(--cover-bottom));overflow:hidden}
  .back-cover,.front-cover{width:463px}
  .spine{width:68px;border-left:1px solid rgba(0,0,0,.18);border-right:1px solid rgba(0,0,0,.18)}

  /* back cover */
  .blurb{position:absolute;left:64px;top:113px;width:335px;font-family:"Questrial",sans-serif;font-size:8.4px;line-height:1.32;color:var(--ivory);text-align:justify}
  .back-mark{float:left;width:72px;margin:2px 8px 6px 0;text-align:center;font-family:"Playfair Display",serif;color:var(--ivory);line-height:.9}
  .back-mark .num{display:block;font-size:62px;color:var(--gold);line-height:.9}
  .back-mark .word{display:block;font-size:21px;letter-spacing:-.5px;line-height:1}
  .back-mark .small{display:block;font-size:11px;line-height:1;margin:-2px 0 -1px}
  .blurb .lead{font-family:"Montserrat",sans-serif;font-weight:600;font-size:10px;color:var(--gold);margin-bottom:2px;text-align:left}
  .blurb p{margin-bottom:5px}
  .blurb .full{clear:left}
  .author-portrait{position:absolute;left:165px;top:296px;width:128px;height:128px;border-radius:50%;background:radial-gradient(circle at 50% 40%,#5b626b,var(--portrait))}
  .bio{position:absolute;left:64px;top:438px;width:335px;font-family:"Questrial",sans-serif;font-size:8.4px;line-height:1.32;color:var(--ivory);text-align:justify}
  .bio p{margin-bottom:5px}
  .code-box{position:absolute;left:315px;top:585px;width:133px;height:84px;background:var(--code-box)}

  /* spine */
  .spine-text{position:absolute;left:50%;top:100px;transform:translateX(-50%);writing-mode:vertical-rl;display:flex;align-items:center;white-space:nowrap}
  .spine-title{font-family:"Playfair Display",serif;font-size:40px;color:var(--gold);letter-spacing:-1px}
  .spine-title small{font-size:20px}
  .spine-sep{width:1px;height:26px;background:var(--ivory);margin:10px 0;writing-mode:horizontal-tb;align-self:center;transform:rotate(90deg)}
  .spine-author{font-family:"Montserrat",sans-serif;font-weight:600;font-size:17px;letter-spacing:5px;color:var(--ivory)}

  /* front cover */
  .accolade{position:absolute;left:0;right:0;top:42px;text-align:center;font-family:"Questrial",sans-serif;font-size:10.5px;color:var(--ivory)}
  .accolade span{display:inline-block;padding:7px 6px;border-top:1px solid var(--rule);border-bottom:1px solid var(--rule)}
  .big-number{position:absolute;left:0;right:0;top:50px;text-align:center;font-family:"Playfair Display",serif;font-size:330px;line-height:1;color:var(--gold)}
  .cover-photo{position:absolute;left:200px;top:118px;width:156px;height:526px;background:linear-gradient(180deg,var(--photo-mid),var(--photo-deep) 60%,#3a2a22);border-radius:40px 40px 6px 6px;opacity:.92}
  .title{position:absolute;left:0;right:0;top:362px;text-align:center;font-family:"Playfair Display",serif;color:var(--ivory);line-height:.85;text-shadow:0 2px 4px rgba(0,0,0,.25)}
  .title .main{display:block;font-size:92px;letter-spacing:-2px}
  .title .joiner{display:block;font-size:42px;margin:-6px 0 -8px}
  .subtitle{position:absolute;left:0;right:0;top:572px;text-align:center;font-family:"Questrial",sans-serif;font-size:14px;color:var(--ivory)}
  .author{position:absolute;left:0;right:0;top:637px;text-align:center;font-family:"Montserrat",sans-serif;font-weight:600;font-size:21px;letter-spacing:6px;color:var(--ivory)}
</style>
</head>
<body>
<main class="wrap">
  <section class="panel back-cover">
    <div class="blurb">
      <div class="back-mark"><span class="num">7</span><span class="word">Laws</span><span class="small">of</span><span class="word">Polish</span></div>
      <p class="lead">Polish is not vanity. It's strategy.</p>
      <p>Like it or not, the way you dress has a huge impact on your life. It doesn't matter how smart you are or how good you are at your job; if people assume you are sloppy and can't be trusted, you're fighting an uphill battle. Most people are climbing this mountain and don't understand why progress is so hard to make - professionally, socially, romantically, or otherwise.</p>
      <p>The good news is - like any other skill - style is something you can learn, practice and improve.</p>
      <p class="full">This book will give you a foundation for understanding how to dress for success and build a lasting wardrobe that works for you. I've used these principles to help thousands of people get raises and promotions, meet their future wives, become the leader of their social circles and significantly improve their confidence.</p>
    </div>
    <div class="author-portrait" role="img" aria-label="Circular portrait photo of the author in a tweed jacket and tie"></div>
    <div class="bio">
      <p>Joel Mackworth was named "Sharpest Gent of the Nation" by Dapperly Journal while studying psychology - and playing basketball - at Halvern University. He then trained to become a bespoke tailor, earned a degree in Menswear Design from the Metro Institute of Apparel in NYC and started a menswear blog that gained millions of readers worldwide.</p>
      <p>After 10 years of working with customers in-person in New York City, Joel combined his experience in bespoke tailoring with his passion for teaching men how to dress for success and expanded his award-winning blog into Threadwell House; a full-service online bespoke tailor shop.</p>
      <p>Today Joel lives in Toronto with his wife Marisol and their daughter Elena where he meets with customers on Parlay from all over the world to refine their style and build their dream wardrobes.</p>
    </div>
    <div class="code-box"></div>
  </section>

  <section class="panel spine">
    <div class="spine-text">
      <span class="spine-title">Laws <small>of</small> Polish</span>
      <span class="spine-sep"></span>
      <span class="spine-author">JOEL MACKWORTH</span>
    </div>
  </section>

  <section class="panel front-cover">
    <p class="accolade"><span>"Sharpest Gent of the Nation" by Dapperly Journal</span></p>
    <div class="big-number">7</div>
    <div class="cover-photo" role="img" aria-label="Full-length photo of the author standing in a rust-brown suit with a black bow tie"></div>
    <h1 class="title"><span class="main">Laws</span><span class="joiner">of</span><span class="main">Polish</span></h1>
    <p class="subtitle">A Closet Map for Triumph</p>
    <p class="author">JOEL MACKWORTH</p>
  </section>
</main>
</body>
</html>
```